Very new and innovative Web design for Property managers of Vacation rentals

We are looking for a new website design for travel agencies and property managers specialised on vacation rentals business, holiday villas and apartments.

The end users of this website are travellers who are looking for a vacation home for their next holiday: this is the reason why the website must be easy to use, attractive, professional, possibly elegant and focused on get new reservations.

This is a draft of our current website: https://intro3.kelumsito.com/
Please consider that we would like to have proposals with a totally different and innovative layout, surprise us!

These are the pages of the website:
• Homepage: feel free to redesign all the homepage as you wish, surprise us with something very new! Please consider that Property manager/Travel agencies usually want to have the opportunity to put in evidence groups of houses with specific characteristics (eg. villas with private swimming pool, apartment in big/small towns, villas with air co, etc…), destinations and tourist areas, and sometimes experiences or activities (please consider that the website layout must be suitable even if some of the previous sections are not used).
• Search page: we’d like to organise the results of the search page in three different ways:
o Grid
o Map
o List
• Property page: to illustrate the characteristics, descriptions, images, …. of the property. It is very important to put in evidence images of the property and to maintain the booking form (and the other call to action bottom – eg. whatsapp) always visible
• Custom pages: static pages composed usually by text, images and call to actions
• Contact us (general form)
• Info request (specific of a property form)
• Booking process
• Blog, organised in four pages:
o Home Page – introduction to the blog
o List of articles
o Single article
o Site Map (presentation of categories and sub-categories)

If possible, we’d prefer to receive the material in Adobe XD or similar so that we can obtain the three versions:
- smartphone
- tablet
- desktop

The website will be then developed in Bootstrap: as a result we’ll need the icons in SVG format (or the library used)

In attachment you can find the map of the website pages

```html
<!DOCTYPE html>
<html lang="en">
<head>
<meta charset="utf-8">
<title>Custom Page – StayNest</title>
<link rel="stylesheet" href="https://fonts.googleapis.com/css2?family=Yanone+Kaffeesatz:wght@300;400;600&family=Poppins:wght@400;500;600&display=swap">
<style>
:root{
  --accent:#1fd494;
  --ink:#1c1c1c;
  --body:#555558;
  --muted:#8a8a8e;
  --white:#ffffff;
  --footer:#1c1b1e;
  --footer-line:#3a393d;
  --footer-text:#d9d9dc;
}
*{margin:0;padding:0;box-sizing:border-box}
html,body{width:1200px;height:2740px;overflow:hidden}
body{position:relative;background:var(--white);font-family:"Poppins",sans-serif;color:var(--body)}
.abs{position:absolute}

/* hero */
.hero{left:0;top:0;width:1200px;height:243px;
  background:linear-gradient(180deg,rgba(20,25,28,.55),rgba(20,25,28,.35)),linear-gradient(100deg,#5c4a3a 0%,#2f5f5c 35%,#2a6a62 55%,#4a5a48 80%,#6b5a3e 100%)}
.brand{display:flex;align-items:center;gap:10px;font-family:"Poppins",sans-serif;font-weight:500;font-size:25px;letter-spacing:1px;color:var(--white)}
.brand .dot{width:20px;height:20px;border-radius:50%;background:var(--accent)}
.topbar{top:17px;display:flex;align-items:center;gap:6px;font-size:11.5px;letter-spacing:.5px;color:var(--white)}
.lang{left:1000px;top:10px;width:106px;height:34px;background:var(--accent);color:var(--white);font-size:10.5px;display:flex;align-items:center;justify-content:center;gap:6px}
.lang .sq{width:13px;height:9px;background:#d9d9e6}
.nav{top:70px;font-size:14px;font-weight:500;letter-spacing:1.2px;color:var(--white)}
.hero-title{left:0;width:1200px;top:144px;text-align:center;font-family:"Yanone Kaffeesatz",sans-serif;font-weight:600;font-size:46px;color:var(--white);letter-spacing:.5px}

/* content */
.crumb{left:93px;top:276px;font-size:11px;color:var(--muted)}
.crumb b{font-weight:400;color:var(--ink)}
.kicker{font-family:"Yanone Kaffeesatz",sans-serif;font-weight:300;font-size:25px;color:var(--ink)}
.title{font-family:"Yanone Kaffeesatz",sans-serif;font-weight:300;font-size:46px;line-height:1.05;color:var(--ink)}
.text{font-size:14px;line-height:22.5px;color:var(--body)}
.photo{border-radius:5px}

/* footer */
.footer{left:0;top:2125px;width:1200px;height:615px;background:var(--footer)}
.f-head{font-size:15px;font-weight:500;letter-spacing:1.2px;color:var(--accent)}
.f-link{font-size:13px;letter-spacing:.8px;color:var(--footer-text)}
.post-title{font-size:12px;font-weight:600;line-height:15px;color:var(--accent)}
.post-date{font-size:12px;color:var(--footer-text)}
.c-head{font-size:15px;font-weight:600;letter-spacing:1.2px;color:var(--accent)}
.c-text{font-size:15px;letter-spacing:.8px;color:var(--white);white-space:nowrap}
.vline{width:1px;height:117px;background:var(--footer-line)}
.legal{left:0;width:1200px;text-align:center;font-size:12px;letter-spacing:.8px;color:var(--white)}
.legal .hl{color:var(--accent)}
</style>
</head>
<body>

<header class="abs hero" role="img" aria-label="Venice canal with boats and historic buildings"></header>
<div class="abs brand" style="left:93px;top:38px"><span class="dot"></span>StayNest</div>
<div class="abs topbar" style="left:814px">
  <svg width="10" height="10" viewBox="0 0 10 10" fill="none" stroke="#fff" stroke-width="1"><circle cx="5" cy="3" r="2"/><path d="M1 9.5c0-2.2 1.8-3.5 4-3.5s4 1.3 4 3.5"/></svg>Login
</div>
<div class="abs topbar" style="left:892px">
  <svg width="11" height="10" viewBox="0 0 11 10"><path d="M5.5 9.5 1.2 5.3A2.6 2.6 0 0 1 5.5 1.7a2.6 2.6 0 0 1 4.3 3.6z" fill="#fff"/></svg>Wish List (0)
</div>
<div class="abs lang"><span class="sq"></span>Language
  <svg width="8" height="6" viewBox="0 0 8 6"><path d="M1 1l3 3 3-3" stroke="#fff" stroke-width="1.5" fill="none"/></svg>
</div>
<nav>
  <div class="abs nav" style="left:537px">Last Minute</div>
  <div class="abs nav" style="left:682px">Special Offers</div>
  <div class="abs nav" style="left:846px">Experience</div>
  <div class="abs nav" style="left:989px">Contact Us</div>
</nav>
<h1 class="abs hero-title">CUSTOM PAGE</h1>

<div class="abs crumb">Home Page &nbsp;/&nbsp; <b>Custom Page</b></div>

<section>
  <div class="abs kicker" style="left:93px;top:340px">But I must explain to you</div>
  <h2 class="abs title" style="left:93px;top:372px;width:390px">How all this mistaken idea of Denouncing</h2>
  <p class="abs text" style="left:93px;top:484px;width:553px">Nam libero tempore, cum soluta nobis est eligendi optio cumque nihil impedit quo minus id quod maxime placeat facere possimus, omnis voluptas assumenda est, omnis dolor repellendus. Temporibus autem quibusdam et aut officiis debitis aut rerum necessitatibus saepe eveniet ut et voluptates repudiandae sint et molestiae non recusandae. Itaque earum rerum hic tenetur a sapiente delectus, ut aut reiciendis voluptatibus maiores alias consequatur aut perferendis doloribus asperiores repellat.</p>
  <div class="abs photo" style="left:675px;top:347px;width:431px;height:291px;background:linear-gradient(180deg,#1c2a5e 0%,#2b3f7e 40%,#9a7a45 70%,#4a3a22 100%)" role="img" aria-label="Illuminated basilica square at night"></div>
  <p class="abs text" style="left:93px;top:657px;width:1013px">Nam libero tempore, cum soluta nobis est eligendi optio cumque nihil impedit quo minus id quod maxime placeat facere possimus, omnis voluptas assumenda est, omnis dolor repellendus. Temporibus autem quibusdam et aut officiis debitis aut rerum necessitatibus saepe eveniet ut et voluptates repudiandae sint et molestiae non recusandae. Itaque earum rerum hic tenetur...</p>
</section>

<section>
  <div class="abs photo" style="left:96px;top:761px;width:432px;height:291px;background:linear-gradient(180deg,#3a7ed0 0%,#8fbbe8 45%,#e8e4da 70%,#5f9a3c 100%)" role="img" aria-label="Leaning tower and cathedral under blue sky"></div>
  <div class="abs kicker" style="left:557px;top:805px">I explain to you</div>
  <h2 class="abs title" style="left:557px;top:835px">Ducimus Qui Praesentium</h2>
  <p class="abs text" style="left:558px;top:895px;width:550px">Nam libero tempore, cum soluta nobis est eligendi optio cumque nihil impedit quo minus id quod maxime placeat facere possimus, omnis voluptas assumenda est, omnis dolor repellendus. Temporibus autem quibusdam et aut officiis debitis aut rerum necessitatibus saepe eveniet ut et voluptates repudiandae sint et molestiae non recusandae.</p>
</section>

<section>
  <div class="abs kicker" style="left:93px;top:1131px">I explain to you</div>
  <h2 class="abs title" style="left:93px;top:1161px">Ducimus Qui Praesentium</h2>
  <p class="abs text" style="left:94px;top:1221px;width:550px">Nam libero tempore, cum soluta nobis est eligendi optio cumque nihil impedit quo minus id quod maxime placeat facere possimus, omnis voluptas assumenda est, omnis dolor repellendus. Temporibus autem quibusdam et aut officiis debitis aut rerum necessitatibus saepe eveniet ut et voluptates repudiandae sint et molestiae non recusandae.</p>
  <div class="abs photo" style="left:676px;top:1087px;width:431px;height:292px;background:linear-gradient(180deg,#d9844e 0%,#c9a07a 35%,#3aa3a6 65%,#1d7d86 100%)" role="img" aria-label="Guest relaxing in a hotel swimming pool"></div>
</section>

<section>
  <div class="abs photo" style="left:96px;top:1431px;width:432px;height:291px;background:linear-gradient(180deg,#7f9ec4 0%,#b7c6d6 30%,#b8946a 60%,#3f4a32 100%)" role="img" aria-label="Ancient amphitheatre at dusk"></div>
  <div class="abs kicker" style="left:557px;top:1475px">I explain to you</div>
  <h2 class="abs title" style="left:557px;top:1505px">Ducimus Qui Praesentium</h2>
  <p class="abs text" style="left:558px;top:1565px;width:550px">Nam libero tempore, cum soluta nobis est eligendi optio cumque nihil impedit quo minus id quod maxime placeat facere possimus, omnis voluptas assumenda est, omnis dolor repellendus. Temporibus autem quibusdam et aut officiis debitis aut rerum necessitatibus saepe eveniet ut et voluptates repudiandae sint et molestiae non recusandae.</p>
</section>

<section>
  <div class="abs kicker" style="left:93px;top:1801px">I explain to you</div>
  <h2 class="abs title" style="left:93px;top:1831px">Ducimus Qui Praesentium</h2>
  <p class="abs text" style="left:94px;top:1891px;width:550px">Nam libero tempore, cum soluta nobis est eligendi optio cumque nihil impedit quo minus id quod maxime placeat facere possimus, omnis voluptas assumenda est, omnis dolor repellendus. Temporibus autem quibusdam et aut officiis debitis aut rerum necessitatibus saepe eveniet ut et voluptates repudiandae sint et molestiae non recusandae.</p>
  <div class="abs photo" style="left:676px;top:1757px;width:431px;height:292px;background:linear-gradient(160deg,#5f86b8 0%,#4a6a6a 35%,#5a7a3e 60%,#233a55 100%)" role="img" aria-label="Lakeside alpine village below mountains"></div>
</section>

<footer class="abs footer"></footer>
<div class="abs brand" style="left:95px;top:2228px"><span class="dot"></span>StayNest</div>
<div class="abs f-link" style="left:95px;top:2285px">Subscribe to our Newsletter</div>
<div class="abs" style="left:95px;top:2311px;width:208px;height:1px;background:var(--footer-text)"></div>
<svg class="abs" style="left:324px;top:2305px" width="40" height="12" viewBox="0 0 40 12" fill="none" stroke="#1fd494" stroke-width="1.3"><path d="M0 6h38M33 1l5 5-5 5"/></svg>
<p class="abs f-link" style="left:95px;top:2335px;width:300px;font-size:12.5px;line-height:17px">Our range of services is very large, and we are constantly expanding it.</p>

<div class="abs f-head" style="left:516px;top:2199px">Navigation</div>
<div class="abs f-link" style="left:518px;top:2239px">Last Minute</div>
<div class="abs f-link" style="left:518px;top:2274px">Special Offers</div>
<div class="abs f-link" style="left:518px;top:2308px">Experience</div>
<div class="abs f-link" style="left:518px;top:2343px">Contact Us</div>

<div class="abs f-head" style="left:791px;top:2199px">Recent posts</div>
<div class="abs" style="left:791px;top:2240px;width:71px;height:61px;background:linear-gradient(180deg,#8aa0a8,#3c8fa8)" role="img" aria-label="Villa pool thumbnail"></div>
<div class="abs post-title" style="left:872px;top:2240px;width:230px">Which construction tool is better to choose?</div>
<div class="abs post-date" style="left:872px;top:2284px">2 November, 2020</div>
<div class="abs" style="left:791px;top:2325px;width:71px;height:61px;background:linear-gradient(180deg,#b48a62,#6a5a4a)" role="img" aria-label="Apartment interior thumbnail"></div>
<div class="abs post-title" style="left:872px;top:2325px;width:230px">Which construction tool is better to choose?</div>
<div class="abs post-date" style="left:872px;top:2369px">2 November, 2020</div>

<svg class="abs" style="left:121px;top:2508px" width="30" height="30" viewBox="0 0 24 24" fill="none" stroke="#1fd494" stroke-width="2"><path d="M5 2h4l2 5-2.5 1.5a11 11 0 0 0 7 7L17 13l5 2v4a2 2 0 0 1-2 2A18 18 0 0 1 3 4a2 2 0 0 1 2-2z"/></svg>
<div class="abs c-head" style="left:165px;top:2484px">Call us</div>
<div class="abs c-text" style="left:165px;top:2505px">+1 555 014 2278 (USA)</div>
<div class="abs vline" style="left:434px;top:2466px"></div>
<svg class="abs" style="left:484px;top:2507px" width="40" height="30" viewBox="0 0 40 30" fill="none" stroke="#1fd494" stroke-width="2.2"><rect x="1.5" y="1.5" width="37" height="27" rx="3"/><path d="M2 3l18 14 18-14"/></svg>
<div class="abs c-head" style="left:536px;top:2484px">Write to us</div>
<div class="abs c-text" style="left:536px;top:2505px">hello@staynest.net</div>
<div class="abs vline" style="left:764px;top:2466px"></div>
<svg class="abs" style="left:825px;top:2500px" width="30" height="42" viewBox="0 0 30 42" fill="none" stroke="#1fd494" stroke-width="2.2"><path d="M15 40S2 24 2 15a13 13 0 0 1 26 0c0 9-13 25-13 25z"/><circle cx="15" cy="15" r="5"/></svg>
<div class="abs c-head" style="left:860px;top:2484px">Office location</div>
<div class="abs c-text" style="left:860px;top:2505px">27 Harbor Ln, Brookvale, NY 10990</div>

<div class="abs" style="left:95px;top:2583px;width:1012px;height:1px;background:var(--footer-line)"></div>
<div class="abs legal" style="top:2608px">Privacy Policies &nbsp;&nbsp;/&nbsp;&nbsp; Reservation Policies &nbsp;&nbsp;/&nbsp;&nbsp; Cookie Policy</div>
<div class="abs legal" style="top:2626px">Copyright © 2021 StayNest. All Rights Reserved. <span class="hl">Powered by StayNest</span></div>
<div class="abs" style="left:578px;top:2663px;width:16px;height:16px;border-radius:50%;background:var(--white)"></div>
<div class="abs" style="left:599px;top:2664px;width:56px;height:14px;border-radius:2px;background:#3f6ee0"></div>

</body>
</html>
```